Business card design needed

I would like a one sided black business card with the information provided above. Refer to my website www.brightvolleyracquets.com.au for an example of colors I have used for my site, would like to keep this consistent for my business cards also, I will upload my logo below.

I am a new small business that provides tennis customers with racquet re stringing, tennis strings and accessories.

Industry/Entity Type

Small Business

Contact Information for Business Card

Bright Volley Tennis

Owen Whitby
Managing Director

brightvolleyracquets@mailbox.example
www.brightvolleyracquets.com.au
0491 726 305

Racquet Restringing/Tennis Strings/Accessories

Requirements
Must have
• Must have my logo and card must be black

```html
<!DOCTYPE html>
<html lang="en">
<head>
<meta charset="utf-8">
<title>Bright Volley Tennis – Business Card</title>
<link href="https://fonts.googleapis.com/css2?family=Source+Sans+3:wght@400;600;700&display=swap" rel="stylesheet">
<style>
  :root {
    --backdrop: #e6e3de;
    --card-black: #050505;
    --lime: #b3d334;
    --accent-blue: #2c5b93;
    --white: #ffffff;
  }
  html, body {
    margin: 0;
    padding: 0;
    width: 1200px;
    height: 750px;
    overflow: hidden;
    background: var(--backdrop);
    font-family: "Source Sans 3", "Myriad Pro", Arial, sans-serif;
  }
  .card {
    position: absolute;
    left: 75px;
    top: 75px;
    width: 1050px;
    height: 597px;
    background: var(--card-black);
    border-radius: 40px;
    overflow: hidden;
  }
  .brand {
    position: absolute;
    left: 60px;
    top: 140px;
    display: flex;
    align-items: center;
    gap: 16px;
  }
  .brand-dot {
    width: 38px;
    height: 38px;
    border-radius: 50%;
    background: var(--lime);
  }
  .brand-name {
    margin: 0;
    font-size: 50px;
    font-weight: 700;
    color: var(--lime);
    letter-spacing: 0.5px;
    line-height: 1;
  }
  .name-marker {
    position: absolute;
    left: 0;
    top: 298px;
    width: 18px;
    height: 87px;
    background: var(--accent-blue);
  }
  .person {
    position: absolute;
    left: 51px;
    top: 304px;
    color: var(--lime);
  }
  .person-name {
    margin: 0;
    font-size: 33px;
    font-weight: 700;
    line-height: 1.1;
  }
  .person-role {
    margin: 2px 0 0;
    font-size: 25px;
    font-weight: 400;
    line-height: 1.2;
  }
  .contact-list {
    position: absolute;
    left: 58px;
    top: 444px;
    margin: 0;
    padding: 0;
    list-style: none;
    color: var(--white);
    font-size: 25px;
  }
  .contact-item {
    display: flex;
    align-items: center;
    height: 43.5px;
  }
  .contact-icon {
    width: 22px;
    height: 22px;
    margin-right: 12px;
    fill: var(--lime);
    flex: none;
  }
  .services {
    position: absolute;
    right: 53px;
    top: 444px;
    margin: 0;
    padding: 0;
    list-style: none;
    text-align: right;
    color: var(--white);
    font-size: 29px;
    line-height: 40px;
  }
  .service::before {
    content: "";
    display: inline-block;
    width: 8px;
    height: 8px;
    background: var(--white);
    margin-right: 10px;
    vertical-align: 0.35em;
  }
</style>
</head>
<body>
  <main class="card">
    <div class="brand">
      <span class="brand-dot" aria-hidden="true"></span>
      <h1 class="brand-name">Bright Volley Tennis</h1>
    </div>

    <div class="name-marker" aria-hidden="true"></div>
    <div class="person">
      <p class="person-name">Owen Whitby</p>
      <p class="person-role">Managing Director</p>
    </div>

    <ul class="contact-list">
      <li class="contact-item">
        <svg class="contact-icon" viewBox="0 0 24 24" aria-hidden="true">
          <path d="M2 9c0-3 5-5 10-5s10 2 10 5v2h-5V9c-1-1-3-1.5-5-1.5S8 8 7 9v2H2z"/>
          <path d="M6 12h12l2 8H4z"/>
        </svg>
        0491 726 305
      </li>
      <li class="contact-item">
        <svg class="contact-icon" viewBox="0 0 24 24" aria-hidden="true">
          <path d="M2 6h20v13H2z M4 8v1l8 5 8-5V8l-8 5z" fill-rule="evenodd"/>
        </svg>
        brightvolleyracquets@mailbox.example
      </li>
      <li class="contact-item">
        <svg class="contact-icon" viewBox="0 0 24 24" aria-hidden="true">
          <circle cx="12" cy="12" r="10"/>
          <path d="M2 12h20M12 2v20M5 6q7 3 14 0M5 18q7-3 14 0" stroke="#050505" stroke-width="1.4" fill="none"/>
        </svg>
        www.brightvolleyracquets.com.au
      </li>
    </ul>

    <ul class="services">
      <li class="service">Racquet Restringing</li>
      <li class="service">Tennis Strings</li>
      <li class="service">Accessories</li>
    </ul>
  </main>
</body>
</html>
```